Modern Business Card

Modern professional business card with more than just logo and demographic info. Something memorable.

We are a trendy/modern chiropractic group with an emphasis on neurology, hence the minimalist-type brain logo. We want to convey that modern and technical aspect with professionalism and the elite nature of our practice environment.

```html
<!DOCTYPE html>
<html lang="en">
<head>
<meta charset="utf-8">
<title>Northgate Chiropractic – Business Card</title>
<link href="https://fonts.googleapis.com/css2?family=Libre+Baskerville:wght@400;700&family=Montserrat:wght@400;500&display=swap" rel="stylesheet">
<style>
  :root {
    --backdrop: #3b3330;
    --card: #1c1c1d;
    --accent: #3f7fce;
    --ink: #ffffff;
    --muted: #6b6b6e;
  }
  * { margin: 0; padding: 0; box-sizing: border-box; }
  html, body {
    width: 1200px;
    height: 716px;
    overflow: hidden;
    background: var(--backdrop);
  }
  .stage {
    position: relative;
    width: 1200px;
    height: 716px;
    display: flex;
    align-items: center;
    justify-content: center;
    gap: 56px;
  }
  .card {
    position: relative;
    width: 520px;
    height: 298px;
    background: var(--card);
    border-radius: 3px;
    box-shadow: 0 14px 30px rgba(0,0,0,0.45);
    overflow: hidden;
  }

  /* Front */
  .card--front {
    display: flex;
    align-items: center;
    justify-content: center;
    gap: 16px;
  }
  .brand-dot {
    width: 34px;
    height: 34px;
    border-radius: 50%;
    background: var(--accent);
    flex: none;
  }
  .brand-name {
    font-family: "Libre Baskerville", serif;
    font-weight: 400;
    color: var(--ink);
    font-size: 25px;
    letter-spacing: 2px;
    line-height: 1.15;
    text-transform: uppercase;
  }

  /* Back */
  .card--back {
    display: flex;
    align-items: center;
    padding: 0 34px 0 40px;
  }
  .back-brand {
    width: 210px;
    display: flex;
    flex-direction: column;
    align-items: center;
    gap: 14px;
  }
  .back-brand .brand-dot {
    width: 70px;
    height: 70px;
  }
  .back-brand .brand-name {
    color: var(--accent);
    font-size: 15px;
    text-align: center;
  }
  .contact {
    margin-left: 40px;
    font-family: "Montserrat", sans-serif;
    color: var(--ink);
  }
  .contact__name {
    font-family: "Libre Baskerville", serif;
    font-weight: 700;
    color: var(--accent);
    font-size: 17px;
    letter-spacing: 0.5px;
    text-transform: uppercase;
  }
  .contact__role {
    font-size: 12px;
    margin-top: 3px;
  }
  .contact__rule {
    width: 200px;
    height: 2px;
    background: var(--accent);
    margin: 9px 0 12px;
  }
  .contact__address {
    font-size: 12.5px;
    line-height: 1.35;
    font-style: normal;
    margin-bottom: 8px;
  }
  .contact__list { list-style: none; }
  .contact__item {
    display: flex;
    align-items: center;
    gap: 8px;
    font-size: 12.5px;
    line-height: 1.55;
  }
  .contact__icon {
    width: 10px;
    height: 10px;
    flex: none;
    fill: none;
    stroke: var(--accent);
    stroke-width: 1.4;
  }
</style>
</head>
<body>
<main class="stage">
  <section class="card card--front" aria-label="Card front">
    <span class="brand-dot"></span>
    <h1 class="brand-name">Northgate<br>Chiropractic</h1>
  </section>

  <section class="card card--back" aria-label="Card back">
    <div class="back-brand">
      <span class="brand-dot"></span>
      <p class="brand-name">Northgate Chiropractic</p>
    </div>
    <div class="contact">
      <h2 class="contact__name">Daniel Mercer</h2>
      <p class="contact__role">Director</p>
      <div class="contact__rule"></div>
      <address class="contact__address">1187 Alder Crest Road<br>Corvallis, OR 97330</address>
      <ul class="contact__list">
        <li class="contact__item">
          <svg class="contact__icon" viewBox="0 0 10 10"><path d="M2 1 L4 1 L4.6 3 L3.4 3.8 Q4.5 6 6.2 6.6 L7 5.4 L9 6 L9 8 Q5 9 2.5 6 Q1 4 2 1 Z"/></svg>
          (541) 555-0148
        </li>
        <li class="contact__item">
          <svg class="contact__icon" viewBox="0 0 10 10"><rect x="0.8" y="2" width="8.4" height="6"/><path d="M0.8 2 L5 5.4 L9.2 2"/></svg>
          hello@northgatechiro.com
        </li>
        <li class="contact__item">
          <svg class="contact__icon" viewBox="0 0 10 10"><circle cx="5" cy="5" r="4.2"/><path d="M0.8 5 H9.2 M5 0.8 Q2.6 5 5 9.2 M5 0.8 Q7.4 5 5 9.2"/></svg>
          www.northgatechiro.com
        </li>
      </ul>
    </div>
  </section>
</main>
</body>
</html>
```